Quorva - corporate Business Card

We need a good look and innovative business card for a new start up company based in Los Angeles called "Quorva". We are in a payment business, including payment card, app, and ewallet. We are expert in online payment and Card not present (CNP) transaction.
We need an innovative, modern business card.

Our logo font is Aero Matics

Target Market(s)

Startup - Bank - Online Payment - Card Manufacturing

Industry/Entity Type

Startup

Contact Information for Business Card

phone: 555 014 7396 - Address: 4172 Marlowe blvd, Brenholt Park, CA 90299

Requirements
Must have
• Message: innovative, professional, expert, high tech, trust, online payment expert, security
Nice to have
• no comment
Should not have
• no Comment

```html
<!DOCTYPE html>
<html lang="en">
<head>
<meta charset="utf-8">
<title>Quorva — Business Card</title>
<link href="https://fonts.googleapis.com/css2?family=Open+Sans:wght@400;600;700&display=swap" rel="stylesheet">
<style>
  :root {
    --brand-red: #b8202f;
    --paper: #ffffff;
    --ink-grey: #6b6b6b;
    --rule-grey: #b9b9b9;
    --stripe-grey: #a7a7a7;
    --backdrop: #2b2b2d;
  }
  * { margin: 0; padding: 0; box-sizing: border-box; }
  html, body { width: 1200px; height: 880px; overflow: hidden; }
  body {
    background: var(--backdrop);
    font-family: "Open Sans", Arial, sans-serif;
    position: relative;
  }
  .card {
    position: absolute;
    width: 560px;
    height: 320px;
    border-radius: 22px;
    overflow: hidden;
    box-shadow: 0 14px 30px rgba(0,0,0,0.45);
  }
  .card-front { left: 70px; top: 90px; background: var(--brand-red); }
  .card-back { left: 570px; top: 470px; background: var(--paper); }

  .wordmark {
    position: absolute;
    display: flex;
    align-items: center;
    gap: 14px;
  }
  .wordmark-dot { border-radius: 50%; flex: none; }
  .wordmark-name { font-weight: 700; letter-spacing: 1px; line-height: 1; }

  .card-front .wordmark { left: 130px; top: 118px; }
  .card-front .wordmark-dot { width: 86px; height: 86px; background: var(--paper); }
  .card-front .wordmark-name { font-size: 70px; color: var(--paper); }

  .card-back .wordmark { left: 40px; top: 96px; }
  .card-back .wordmark-dot { width: 70px; height: 70px; background: var(--brand-red); }
  .card-back .wordmark-name { font-size: 54px; color: var(--brand-red); }

  .holder {
    position: absolute;
    right: 36px; top: 28px;
    width: 190px;
    text-align: right;
    border-bottom: 1px solid var(--rule-grey);
    padding-bottom: 4px;
  }
  .holder-name { color: var(--brand-red); font-weight: 700; font-size: 21px; line-height: 1.1; }
  .holder-title { color: var(--ink-grey); font-size: 14px; }

  .address {
    position: absolute;
    right: 36px; top: 92px;
    text-align: right;
    color: var(--ink-grey);
    font-size: 14px;
    font-style: normal;
    line-height: 1.4;
  }
  .divider {
    position: absolute;
    left: 40px; top: 200px;
    width: 484px;
    border-top: 1px solid var(--rule-grey);
  }
  .contacts {
    position: absolute;
    left: 40px; top: 208px;
    list-style: none;
    color: var(--ink-grey);
    font-size: 15px;
  }
  .contacts li { display: flex; align-items: center; gap: 7px; line-height: 23px; }
  .contact-icon { width: 17px; height: 17px; flex: none; }
  .base-band { position: absolute; left: 0; bottom: 0; }
</style>
</head>
<body>

  <section class="card card-front" aria-label="Card front">
    <div class="wordmark">
      <span class="wordmark-dot"></span>
      <span class="wordmark-name">quorva</span>
    </div>
  </section>

  <section class="card card-back" aria-label="Card back">
    <div class="wordmark">
      <span class="wordmark-dot"></span>
      <span class="wordmark-name">quorva</span>
    </div>

    <div class="holder">
      <p class="holder-name">Daniel Hale</p>
      <p class="holder-title">Managing Director</p>
    </div>

    <address class="address">
      4172 Marlowe blvd<br>Brenholt Park, CA 90299
    </address>

    <div class="divider"></div>

    <ul class="contacts">
      <li>
        <svg class="contact-icon" viewBox="0 0 20 20" aria-hidden="true">
          <circle cx="10" cy="10" r="10" fill="var(--brand-red)"/>
          <path d="M6 8.5c0-1.5 2-2.5 4-2.5s4 1 4 2.5l-1.6.6-.6-1.3h-3.6l-.6 1.3z M7 10h6l1 4H6z" fill="#fff"/>
        </svg>
        555 014 7396
      </li>
      <li>
        <svg class="contact-icon" viewBox="0 0 20 20" aria-hidden="true">
          <circle cx="10" cy="10" r="10" fill="var(--brand-red)"/>
          <rect x="5" y="6.5" width="10" height="7" fill="#fff"/>
          <path d="M5 6.5l5 4 5-4" fill="none" stroke="var(--brand-red)" stroke-width="1"/>
        </svg>
        hello@quorvamail.com
      </li>
    </ul>

    <svg class="base-band" width="560" height="60" viewBox="0 0 560 60" aria-hidden="true">
      <polygon points="0,22 382,22 382,28 0,28" fill="var(--stripe-grey)"/>
      <path d="M0,36 L384,36 Q392,36 392,28 L392,10 Q392,2 400,2 L560,2 L560,60 L0,60 Z" fill="var(--brand-red)"/>
    </svg>
  </section>

</body>
</html>
```